Wrenfield Home Care Retractable Banner Design

Retractable Banner Design
We need a pull up retractable banner design
85 x 206 cm.
We need the banner to use at expo's, information sessions, presentations, recruitment days. Needs to be attractive to our elderly client's and staff (care workers)
Phone number needs to be on 08 7394 2056
Website also needs to be on the banner : wrenfieldhomecare.com.au

Target Market(s)

35 +

Industry/Entity Type

aged care / community

Requirements
Must have
• Colours, fonts and logo as detailed in upload

```html
<!DOCTYPE html>
<html lang="en">
<head>
<meta charset="utf-8">
<title>Wrenfield Home Care – Pull Up Banner</title>
<link href="https://fonts.googleapis.com/css2?family=Poppins:wght@400;500;600;700;800&display=swap" rel="stylesheet">
<style>
  :root{
    --stage:#808080;
    --paper:#ffffff;
    --brand-red:#8e0e2b;
    --brand-pink:#c46375;
    --ink:#1f1f1f;
    --band-grey:#dadada;
    --rule:#9a9a9a;
  }
  *{box-sizing:border-box;margin:0;padding:0}
  html,body{width:1200px;height:1200px;overflow:hidden;background:var(--stage);font-family:"Poppins",sans-serif;color:var(--ink)}
  .banner{position:absolute;left:382px;top:72px;width:436px;height:1057px;background:var(--paper);overflow:hidden}
  .backdrop{position:absolute;inset:0;width:436px;height:1057px}
  .abs{position:absolute}
  .center-text{left:0;right:0;text-align:center;line-height:1;white-space:nowrap}

  .brand-mark{left:119px;top:38px;width:64px;height:64px;border-radius:50%;background:var(--brand-red)}
  .brand-name{left:189px;top:36px;font-weight:400;font-size:23px;line-height:25px;color:var(--brand-red)}

  .hero-photo{left:78px;top:144px;width:280px;height:280px;border-radius:50%;
    background:radial-gradient(circle at 60% 45%,#d9cfc4 0%,#b8b4b0 40%,#5f86b8 75%,#e3e0da 100%)}

  .headline-kicker{top:455px;font-size:31px;font-weight:800;color:var(--brand-red);letter-spacing:.3px}
  .headline-main{top:486px;font-size:58px;font-weight:800;color:var(--ink)}
  .headline-sub{top:541px;font-size:25px;font-weight:700;color:var(--ink)}
  .divider-dots{left:194px;top:579px;width:47px;height:6px;
    background:repeating-linear-gradient(90deg,var(--brand-red) 0 6.5px,transparent 6.5px 8px)}
  .intro{top:593px;font-size:17px;font-weight:400;line-height:20.5px}
  .intro-rule{left:75px;top:641px;width:286px;height:1px;background:var(--rule)}
  .ownership{top:649px;font-size:17px;font-weight:700;color:var(--brand-red)}

  .service{border:1px solid #444;border-radius:10px;background:var(--paper);height:69px;
    display:flex;align-items:center;font-size:14px;line-height:17px;font-weight:400;color:var(--ink)}
  .service-left{left:63px;width:128px;padding-left:24px}
  .service-right{left:241px;width:156px;padding-left:27px}
  .row-1{top:684px}.row-2{top:762px}
  .service-dot{width:28px;height:18px;border-radius:50%}
  .dot-dark{background:#333}.dot-red{background:var(--brand-red)}

  .recruit{left:64px;top:845px;width:334px;height:83px;border:1px solid #444;border-radius:10px;overflow:hidden;background:var(--paper)}
  .recruit-band{position:absolute;left:38px;top:0;right:0;height:27px;background:var(--band-grey);
    clip-path:polygon(14px 0,100% 0,100% 100%,0 100%,0 60%)}
  .recruit-title{position:absolute;left:70px;top:5px;font-size:19px;font-weight:700;line-height:1;white-space:nowrap;letter-spacing:-.2px}
  .recruit-title span{color:var(--brand-red)}
  .recruit-body{position:absolute;left:50px;top:33px;width:280px;font-size:10px;line-height:12.2px;font-weight:400}
  .megaphone{left:0;top:866px;width:75px;height:118px;
    background:linear-gradient(160deg,#c0182e 0%,#a3142a 40%,#eeeeee 70%,#d8c3b5 100%);
    clip-path:polygon(0 14%,70% 0,75% 55%,40% 58%,38% 100%,0 100%)}
  .recruit-sparks{left:78px;top:868px}

  .cta-pill{left:70px;top:936px;width:296px;height:32px;border-radius:16px;background:#2a2a2a;border:1px solid #555;
    color:#fff;font-size:15.5px;font-weight:600;display:flex;align-items:center;justify-content:center;z-index:2}
  .contact-panel{left:32px;top:954px;width:375px;height:103px;background:var(--brand-red);border-radius:31px 31px 0 0}
  .contact-phone{top:980px;font-size:28px;font-weight:700;color:#fff;display:flex;justify-content:center;align-items:center;gap:6px}
  .phone-icon{width:24px;height:24px;border-radius:50%;background:#2a2a2a;display:inline-flex;align-items:center;justify-content:center}
  .contact-web{top:1011px;font-size:18px;font-weight:600;color:#fff;letter-spacing:1.4px}
</style>
</head>
<body>
<main class="banner">
  <svg class="backdrop" viewBox="0 0 436 1057" aria-hidden="true">
    <circle cx="-92" cy="267" r="177" fill="var(--brand-pink)"/>
    <circle cx="-109" cy="267" r="177" fill="var(--brand-red)"/>
    <circle cx="528" cy="267" r="177" fill="var(--brand-pink)"/>
    <circle cx="545" cy="267" r="177" fill="var(--brand-red)"/>
    <circle cx="218" cy="284" r="169" fill="var(--paper)"/>
    <circle cx="218" cy="284" r="160" fill="var(--brand-red)"/>
  </svg>

  <div class="abs brand-mark"></div>
  <div class="abs brand-name">Wrenfield<br>Home Care</div>

  <div class="abs hero-photo" role="img" aria-label="Photo of a smiling care worker in blue scrubs helping an elderly man read a book at home"></div>

  <h1 class="abs center-text headline-kicker">COMPASSIONATE</h1>
  <div class="abs center-text headline-main">CARE</div>
  <div class="abs center-text headline-sub">Where You Feel at Home</div>
  <div class="abs divider-dots"></div>
  <p class="abs center-text intro">Supporting Independence and<br>Dignity for Our Clients</p>
  <div class="abs intro-rule"></div>
  <p class="abs center-text ownership">Local and family owned</p>

  <div class="abs service service-left row-1">Personal<br>Care and<br>Assistance</div>
  <div class="abs service service-right row-1">Companionship<br>and Social<br>Support</div>
  <div class="abs service service-left row-2">Meal<br>Preparation &amp;<br>Home Help</div>
  <div class="abs service service-right row-2">Tailored Care<br>Plans for Every<br>Need</div>
  <span class="abs service-dot dot-dark" style="left:46px;top:710px"></span>
  <span class="abs service-dot dot-red" style="left:226px;top:710px"></span>
  <span class="abs service-dot dot-red" style="left:46px;top:788px"></span>
  <span class="abs service-dot dot-dark" style="left:226px;top:788px"></span>

  <section class="abs recruit">
    <div class="recruit-band"></div>
    <h2 class="recruit-title">JOIN OUR <span>CARING TEAM!</span></h2>
    <p class="recruit-body">We’re looking for compassionate individuals to make a difference in our clients’ lives. Flexible hours, rewarding work, and a supportive team await you.</p>
  </section>
  <div class="abs megaphone" role="img" aria-label="Hand holding a red and white megaphone"></div>

  <div class="abs cta-pill">Book your free consultation Today</div>
  <div class="abs contact-panel"></div>
  <div class="abs center-text contact-phone">
    <span class="phone-icon">
      <svg width="13" height="13" viewBox="0 0 24 24" aria-hidden="true"><path fill="#fff" d="M6.6 10.8a15.1 15.1 0 0 0 6.6 6.6l2.2-2.2a1 1 0 0 1 1-.25 11.4 11.4 0 0 0 3.6.57 1 1 0 0 1 1 1V20a1 1 0 0 1-1 1A17 17 0 0 1 3 4a1 1 0 0 1 1-1h3.5a1 1 0 0 1 1 1c0 1.25.2 2.45.57 3.57a1 1 0 0 1-.25 1z"/></svg>
    </span>08 7394 2056
  </div>
  <div class="abs center-text contact-web">wrenfieldhomecare.com.au</div>
</main>
</body>
</html>
```